I need a flyer made , the flyer can be one page or two pages or three pages . I will be posting this on Instagram and social media platforms. I am a luxury home builder , I am looking to hire a construction project manager . Below are some examples and ideas what can be on the flyer

We’re looking for a construction project manager who’s passionate about building luxury homes at the highest standards
We’re hiring construction project manager
* Experience 5+ years in residential project management with a strong portfolio of completed homes.
* location : Bergen County NJ
* excellent leadership skills, leads teams with confidence and clarity
* communicates seamlessly with architects , engineers, designers and clients
*knows how to manage budgets and timelines without compromising quality
*solves problems with a positive solution first mindset
* pays attention to every detail because in luxury the small things are the big things

Apply now , link in bio or DM to connect.

My logo is attached, my web site www.velstridebuilders.com
My style is modern but still warm and inviting. I like a clean classy look .

Please don’t add any images of chairs or people to the flyer , I do not want people on my flyer. Do not add standard images of offices and houses , we are luxury builders , we build homes over 2 million dollars. Keep a classy , simple modern look . High end .

You can add a white hard hat with my logo on it for a image , this is a suggestion does not have to be on my flyer ,

```html
<!DOCTYPE html>
<html lang="en">
<head>
<meta charset="utf-8">
<title>Velstride Builders — Hiring Construction Project Manager</title>
<link href="https://fonts.googleapis.com/css2?family=Poppins:wght@300;400;500;700;800&display=swap" rel="stylesheet">
<style>
  :root {
    --backdrop: #cdd3da;
    --navy-deep: #161c26;
    --navy: #232b38;
    --slate: #3a4150;
    --warm-glow: #5a4a36;
    --white: #ffffff;
    --soft-white: #e6e8ec;
    --muted: #b9bec7;
    --rule: rgba(255,255,255,0.55);
    --ink: #15171c;
  }
  * { margin: 0; padding: 0; box-sizing: border-box; }
  html, body {
    width: 1200px; height: 655px; overflow: hidden;
    background: var(--backdrop);
    font-family: "Poppins", sans-serif;
  }
  .canvas { position: relative; width: 1200px; height: 655px; }

  .panel {
    position: absolute; top: 84px;
    width: 489px; height: 489px;
    overflow: hidden;
    color: var(--white);
  }
  .panel--cover { left: 94px; }
  .panel--details { left: 596px; }

  .panel__photo {
    position: absolute; inset: 0;
    background:
      radial-gradient(ellipse 45% 30% at 75% 55%, rgba(140,110,70,0.35), transparent 70%),
      radial-gradient(ellipse 60% 25% at 50% 90%, rgba(70,80,90,0.5), transparent 70%),
      linear-gradient(160deg, var(--navy) 0%, var(--navy-deep) 55%, #1b2027 100%);
  }
  .panel--details .panel__photo::after {
    content: ""; position: absolute; inset: 0;
    background: rgba(22,27,36,0.45);
  }

  .panel__frame {
    position: absolute; left: 18px; top: 18px; right: 18px; bottom: 18px;
    border: 1px solid var(--rule);
  }

  .brand {
    position: absolute; top: 30px; left: 0; right: 0;
    text-align: center;
    font-weight: 400; font-size: 24px; letter-spacing: 0.08em;
    color: var(--white);
  }

  .website {
    position: absolute; top: 446px; left: 0; right: 0;
    text-align: center;
    font-weight: 300; font-size: 13px; letter-spacing: 0.32em;
    color: var(--muted);
  }

  .cover-title { position: absolute; top: 176px; left: 0; right: 0; text-align: center; }
  .cover-title__lead {
    display: block;
    font-weight: 400; font-size: 50px; line-height: 1; letter-spacing: -0.03em;
    margin-left: -10px;
  }
  .cover-title__main {
    display: block;
    font-weight: 800; font-size: 84px; line-height: 1; letter-spacing: -0.05em;
    margin-top: -2px;
  }

  .intro {
    position: absolute; top: 92px; left: 20px; right: 20px;
    text-align: center;
    font-weight: 500; font-size: 13.4px; line-height: 1.2;
  }
  .role-title {
    position: absolute; top: 146px; left: 0; right: 0;
    text-align: center;
    font-weight: 300; font-size: 23px; line-height: 1;
    letter-spacing: -0.01em;
  }
  .requirements {
    position: absolute; top: 213px; left: 32px; width: 425px;
    list-style: none;
  }
  .requirements li {
    position: relative;
    height: 19.4px; line-height: 19px;
    padding-left: 14px;
    font-weight: 300; font-size: 8.6px;
    color: var(--soft-white);
    border-bottom: 1px solid rgba(255,255,255,0.5);
    white-space: nowrap;
  }
  .requirements li::before {
    content: ""; position: absolute; left: 1px; top: 7px;
    width: 5px; height: 5px; border-radius: 50%;
    background: var(--white);
  }

  .apply-band {
    position: absolute; top: 391px; left: 40px; width: 422px; height: 30px;
    background: linear-gradient(90deg, rgba(255,255,255,0.15) 0%, rgba(255,255,255,0.85) 30%, #fff 50%, rgba(255,255,255,0.85) 70%, rgba(255,255,255,0.15) 100%);
    text-align: center; color: var(--ink);
  }
  .apply-band__cta { display: block; font-weight: 700; font-size: 11px; line-height: 1; padding-top: 5px; }
  .apply-band__note { display: block; font-weight: 400; font-size: 8.5px; line-height: 1.1; }
</style>
</head>
<body>
<main class="canvas">

  <section class="panel panel--cover">
    <div class="panel__photo" role="img" aria-label="Night view of a modern luxury home with glass walls, lit terrace and pool"></div>
    <div class="panel__frame"></div>
    <div class="brand">Velstride Builders</div>
    <h1 class="cover-title">
      <span class="cover-title__lead">We’re</span>
      <span class="cover-title__main">Hiring</span>
    </h1>
    <div class="website">www.velstridebuilders.com</div>
  </section>

  <section class="panel panel--details">
    <div class="panel__photo" role="img" aria-label="Night view of a modern luxury home with glass walls, lit terrace and pool"></div>
    <div class="panel__frame"></div>
    <div class="brand">Velstride Builders</div>
    <p class="intro">We’re looking for a construction project manager who’s passionate about building luxury homes at the highest standards</p>
    <h2 class="role-title">WE’RE HIRING<br>CONSTRUCTION PROJECT MANAGER</h2>
    <ul class="requirements">
      <li>Experience 5+ years in residential project management with a strong portfolio of completed homes</li>
      <li>Location : Bergen County NJ</li>
      <li>Excellent leadership skills, leads teams with confidence and clarity</li>
      <li>Communicates seamlessly with architects, engineers, designers and clients</li>
      <li>Knows how to manage budgets and timelines without compromising quality</li>
      <li>Solves problems with a positive solution first mindset</li>
      <li>Pays attention to every detail because in luxury the small things are the big things</li>
    </ul>
    <div class="apply-band">
      <span class="apply-band__cta">APPLY NOW,</span>
      <span class="apply-band__note">LINK IN BIO OR DM TO CONNECT</span>
    </div>
    <div class="website">www.velstridebuilders.com</div>
  </section>

</main>
</body>
</html>
```